Website for IT consulting Company

I need a website upgrade, the existing site content is ok, I would also like to add a testimonial page, the site should be something that is easy for us to update content. You use the content from www.kelvanbrook.com as an example. I will also post update logo and artwork. I also need a contact form with some type of validation or captcha.

I added Coded to the Project

Please omit Address maps

Target Market(s)

small business, service oriented companies. We provide IT Consulting, support and mangement

Industry/Entity Type

Information Technology

Coding

Number of Pages Required

1 page

Font styles to use
Serif
Sans Serif

Requirements
Must have
• Contain logo attached, and content from existing web site www.kelvanbrook.com.
• Also need to update content easily, and be movable to different platforms.
• There is a catch phrase
• "Let us worry about your technology…” “ so you don’t have to!”
• Should be included.
Nice to have
• Testimonial page, Project page where we can post new and past projects and pictures
Should not have
• none

```html
<!DOCTYPE html>
<html lang="en">
<head>
<meta charset="utf-8">
<title>Kelvanbrook Technology Group</title>
<link href="https://fonts.googleapis.com/css2?family=Exo+2:ital,wght@0,600;0,800;1,600;1,800&family=Arimo:wght@400;700&family=Tinos&display=swap" rel="stylesheet">
<style>
:root{
  --black:#000;
  --blue:#1b8fd8;
  --blue-dark:#0f6fb3;
  --blue-light:#3cb0f0;
  --ink:#1a1a1a;
  --grey-bg:#e9e9e9;
  --grey-panel:#8e8e8e;
  --grey-line:#a0a0a0;
  --footer:#1f2226;
  --white:#fff;
  --head:"Exo 2",sans-serif;
  --body:Arimo,Arial,sans-serif;
  --serif:Tinos,"Times New Roman",serif;
}
*{margin:0;padding:0;box-sizing:border-box}
html,body{width:1200px;height:2557px;overflow:hidden}
body{font-family:var(--body);color:var(--ink);background:var(--white);position:relative}
.abs{position:absolute}

/* header */
.site-header{position:absolute;top:0;left:0;width:1200px;height:124px;background:var(--black)}
.brand{position:absolute;left:82px;top:30px;display:flex;align-items:center;gap:14px}
.brand-mark{width:52px;height:52px;background:var(--blue)}
.brand-name{font-family:var(--head);font-weight:800;font-size:48px;color:var(--white);letter-spacing:1px}
.follow{position:absolute;right:90px;top:14px;display:flex;align-items:center;gap:8px;color:var(--white);font-family:var(--head);font-style:italic;font-weight:800;font-size:19px}
.follow .sq{width:27px;height:27px;background:#d9d9d9;margin-left:4px}
.contact-strip{position:absolute;right:82px;top:68px;display:flex;align-items:center;gap:16px;color:var(--white);font-family:var(--head);font-weight:800;font-style:italic;font-size:22px}
.ico-box{width:40px;height:40px;background:var(--blue);display:flex;align-items:center;justify-content:center}

/* nav */
.main-nav{position:absolute;top:124px;left:0;width:1200px;height:55px;background:linear-gradient(#3bb1ee,#1783cc)}
.main-nav a{position:absolute;top:16px;font-family:var(--head);font-style:italic;font-weight:800;font-size:19px;color:var(--white);text-decoration:none;letter-spacing:.5px}
.main-nav a.active{color:#16304a}

/* hero */
.hero{position:absolute;top:179px;left:0;width:1200px;height:533px;background:radial-gradient(ellipse at 40% 45%,#5d6063,#2b2d30 75%)}
.hero-arrow{position:absolute;top:233px;width:40px;height:36px;background:#555;border:1px solid #777}
.hero-caption{position:absolute;left:0;bottom:0;width:1200px;height:56px;background:rgba(0,0,0,.45);text-align:center;font-family:var(--head);font-style:italic;font-weight:800;font-size:34px;color:var(--white);line-height:56px}
.hero-caption span{color:var(--blue-light)}

/* welcome */
.welcome{position:absolute;top:712px;left:0;width:1200px;height:266px;text-align:center}
.section-title{font-family:var(--head);font-style:italic;font-weight:800;font-size:29px;letter-spacing:.5px}
.section-title span{color:var(--blue)}
.rule{width:80px;height:3px;background:var(--blue);margin:10px auto 0}
.welcome .section-title{margin-top:44px}
.welcome p{width:1040px;margin:20px auto 0;font-size:14.5px;line-height:26px;color:#222}
.more{display:inline-block;margin-top:16px;font-family:var(--head);font-style:italic;font-weight:800;font-size:15px;color:var(--blue-dark);text-decoration:underline}

/* services */
.services{position:absolute;top:978px;left:0;width:1200px;height:576px;background:var(--grey-bg)}
.services .section-title{position:absolute;top:46px;width:100%;text-align:center}
.services svg{position:absolute;top:0;left:0}
.svc-label{font-family:var(--head);font-weight:800;font-size:17px;fill:#222}

/* panels */
.panel{position:absolute;top:1554px;height:386px}
.panel-support{left:0;width:605px;background:linear-gradient(#1e95dc,#1277c0)}
.panel-outsource{left:605px;width:595px;background:linear-gradient(#a9a9a9,#7d7d7d)}
.notch{position:absolute;top:1554px;left:584px;width:0;height:0;border-left:22px solid transparent;border-right:22px solid transparent;border-top:32px solid var(--grey-bg)}
.panel h3{position:absolute;top:62px;font-family:var(--head);font-style:italic;font-weight:800;font-size:25px;color:var(--white)}
.panel h3 i{display:inline-block;width:30px;height:30px;vertical-align:-5px;margin-right:12px;background:rgba(255,255,255,.85)}
.panel .divider{position:absolute;top:110px;height:1px;background:rgba(255,255,255,.35)}
.panel .photo{position:absolute;top:130px;width:205px;height:184px;border:3px solid rgba(255,255,255,.7)}
.panel p{position:absolute;top:130px;width:260px;font-size:14.5px;line-height:26px;color:var(--white)}
.btn{position:absolute;top:278px;width:152px;height:38px;font-family:var(--serif);font-size:17px;color:var(--white);display:flex;align-items:center;justify-content:center;gap:10px}

/* cta */
.cta{position:absolute;top:1940px;left:0;width:1200px;height:245px;text-align:center}
.cta h2{margin-top:40px;font-family:var(--head);font-style:italic;font-weight:800;font-size:35px;color:#111}
.cta h3{margin-top:4px;font-family:var(--head);font-style:italic;font-weight:800;font-size:29px;color:#111}
.call-btn{position:absolute;left:472px;top:150px;width:220px;height:50px;background:linear-gradient(#9a9a9a,#5e5e5e);border-radius:6px;display:flex;align-items:center;gap:8px;padding-left:10px;color:var(--white);font-family:var(--head);font-style:italic;font-weight:800;font-size:18px;line-height:20px;text-align:left}
.call-btn .sq{position:absolute;right:-36px;top:0;width:50px;height:50px;background:var(--blue)}

/* footer */
.site-footer{position:absolute;top:2185px;left:0;width:1200px;height:327px;background:linear-gradient(#2c2f33,#17191c)}
.fcol{position:absolute;top:58px;color:#e6e6e6;font-size:14px}
.fcol h4{font-family:var(--head);font-style:italic;font-weight:800;font-size:19px;color:var(--white);margin-bottom:18px}
.fcol h4 span{color:var(--blue-light)}
.fcol ul{list-style:none}
.quick li{line-height:25px;padding-left:18px;position:relative}
.quick li::before{content:"";position:absolute;left:0;top:10px;width:5px;height:5px;border-radius:50%;background:var(--blue-light)}
.contact-col .line{line-height:22px}
.contact-col .row{display:flex;align-items:center;gap:12px;margin-top:12px}
.social li{display:flex;align-items:center;gap:16px;height:44px}
.social .sq{width:30px;height:30px;background:#d0d0d0}
.footer-mark{position:absolute;left:900px;top:60px;display:flex;flex-direction:column;align-items:center;gap:14px}
.footer-mark .sq{width:150px;height:150px;background:var(--blue);opacity:.9}
.footer-mark span{font-family:var(--head);font-weight:800;font-size:26px;color:#6f7377}
.copyright{position:absolute;top:2512px;left:0;width:1200px;height:45px;background:linear-gradient(#2aa0e4,#1480c8);color:var(--white);text-align:center;font-size:15px;line-height:45px}
</style>
</head>
<body>

<header class="site-header">
  <div class="brand"><div class="brand-mark"></div><div class="brand-name">KELVANBROOK</div></div>
  <div class="follow">Follow Us On <span class="sq"></span><span class="sq"></span><span class="sq"></span><span class="sq"></span></div>
  <div class="contact-strip">
    <span class="ico-box"><svg width="22" height="22" viewBox="0 0 24 24"><path d="M6.6 10.8a15 15 0 0 0 6.6 6.6l2.2-2.2a1 1 0 0 1 1-.25 11.4 11.4 0 0 0 3.6.57 1 1 0 0 1 1 1V20a1 1 0 0 1-1 1A17 17 0 0 1 3 4a1 1 0 0 1 1-1h3.5a1 1 0 0 1 1 1c0 1.25.2 2.45.57 3.57a1 1 0 0 1-.25 1z" fill="#fff"/></svg></span>
    <span>(555) 240-7318</span>
    <span class="ico-box"><svg width="22" height="22" viewBox="0 0 24 24"><circle cx="12" cy="8" r="5" fill="#fff"/><path d="M3 22c0-5 4-8 9-8s9 3 9 8z" fill="#fff"/></svg></span>
    <span>SUPPORT</span>
  </div>
</header>

<nav class="main-nav">
  <a class="active" style="left:99px">HOME</a>
  <a style="left:252px">ABOUT US</a>
  <a style="left:441px">SERVICES</a>
  <a style="left:632px">CLIENTS</a>
  <a style="left:808px">CAREERS</a>
  <a style="left:991px">CONTACT US</a>
</nav>

<section class="hero">
  <div class="abs" role="img" aria-label="Businessman in a suit facing a chalkboard covered with technology and business sketches" style="inset:0"></div>
  <div class="hero-arrow" style="left:4px"><svg width="38" height="34" viewBox="0 0 38 34"><path d="M22 10l-7 7 7 7" stroke="#fff" stroke-width="3" fill="none"/></svg></div>
  <div class="hero-arrow" style="right:4px"><svg width="38" height="34" viewBox="0 0 38 34"><path d="M16 10l7 7-7 7" stroke="#fff" stroke-width="3" fill="none"/></svg></div>
  <div class="hero-caption">Let Us Worry About Your Technology... <span>So You Don't Have To!</span></div>
</section>

<section class="welcome">
  <h2 class="section-title">WELCOME TO KELVANBROOK <span>TECHNOLOGY GROUP, INC</span></h2>
  <div class="rule"></div>
  <p>Kelvanbrook Technology Group, Inc. was established in 1991. Our mission is helping businesses and individuals realize a Return on Investment by implementing today's advanced technologies. As a small business we understand the importance of technology and personalized attention.&nbsp; Every member of our support team has worked with both large and small companies supporting a multitude of applications, networks and environments.</p>
  <a class="more">READ MORE</a>
</section>

<section class="services">
  <svg width="1200" height="576" viewBox="0 0 1200 576">
    <g stroke="#bdbdbd" stroke-width="2" stroke-dasharray="3 4" fill="none">
      <line x1="622" y1="181" x2="600" y2="369"/>
      <line x1="498" y1="220" x2="533" y2="379"/>
      <line x1="733" y1="220" x2="667" y2="379"/>
      <line x1="392" y1="283" x2="460" y2="417"/>
      <line x1="839" y1="283" x2="740" y2="417"/>
      <line x1="315" y1="360" x2="410" y2="462"/>
      <line x1="915" y1="374" x2="790" y2="462"/>
      <line x1="269" y1="484" x2="380" y2="520"/>
      <line x1="958" y1="484" x2="820" y2="520"/>
    </g>
    <circle cx="600" cy="604" r="235" fill="#fff" stroke="#9c9c9c" stroke-width="12"/>
    <g fill="#fff" stroke="#9c9c9c" stroke-width="3">
      <circle cx="600" cy="369" r="8"/><circle cx="533" cy="379" r="8"/><circle cx="667" cy="379" r="8"/>
      <circle cx="460" cy="417" r="8"/><circle cx="740" cy="417" r="8"/><circle cx="410" cy="462" r="8"/>
      <circle cx="790" cy="462" r="8"/><circle cx="380" cy="520" r="8"/><circle cx="820" cy="520" r="8"/>
    </g>
    <rect x="580" y="410" width="40" height="40" fill="#1b8fd8"/>
    <text x="600" y="525" text-anchor="middle" font-family="Exo 2, sans-serif" font-weight="800" font-size="44" fill="#7a7a7a">KELVANBROOK</text>
    <g fill="#1b8fd8" stroke="#fff" stroke-width="4">
      <circle cx="622" cy="181" r="50"/><circle cx="498" cy="220" r="50"/><circle cx="733" cy="220" r="50"/>
      <circle cx="392" cy="283" r="50"/><circle cx="839" cy="283" r="50"/><circle cx="315" cy="360" r="50"/>
      <circle cx="915" cy="374" r="50"/><circle cx="269" cy="484" r="50"/><circle cx="958" cy="484" r="50"/>
    </g>
    <g fill="none" stroke="#fff" stroke-width="4">
      <rect x="604" y="160" width="36" height="12" rx="3"/><rect x="604" y="176" width="36" height="12" rx="3"/><rect x="604" y="192" width="36" height="10" rx="3"/>
      <line x1="491" y1="208" x2="491" y2="232"/><line x1="505" y1="208" x2="505" y2="232"/>
      <rect x="712" y="204" width="32" height="24" rx="2"/><rect x="748" y="212" width="12" height="20" rx="2"/>
      <line x1="392" y1="270" x2="380" y2="305"/><line x1="392" y1="270" x2="404" y2="305"/><path d="M378 268a18 18 0 0 0 0 20M406 268a18 18 0 0 1 0 20"/>
      <path d="M822 300l30-30M826 270h18v18"/>
      <circle cx="308" cy="350" r="8"/><path d="M294 378c0-10 6-16 14-16s14 6 14 16"/><rect x="318" y="356" width="18" height="14"/>
      <path d="M895 374a26 26 0 0 1 40 0M902 382a16 16 0 0 1 26 0"/><rect x="897" y="388" width="36" height="10" rx="3"/>
      <rect x="250" y="470" width="38" height="24" rx="2"/><line x1="244" y1="500" x2="294" y2="500"/>
      <path d="M958 462l18 7v14c0 12-8 19-18 23-10-4-18-11-18-23v-14z"/>
    </g>
    <g class="svc-label">
      <text class="svc-label" x="622" y="140" text-anchor="middle">DISASTER RECOVERY</text>
      <text class="svc-label" x="225" y="198">AUDIO/VIDEO MULTIMEDIA</text>
      <text class="svc-label" x="783" y="189">WEB DESIGN</text>
      <text class="svc-label" x="128" y="274">TELECOMMUNICATIONS</text>
      <text class="svc-label" x="900" y="274">NETWORK CABLING</text>
      <text class="svc-label" x="250" y="360" text-anchor="end">NETWORK</text>
      <text class="svc-label" x="250" y="377" text-anchor="end">ADMINISTRATION</text>
      <text class="svc-label" x="982" y="366">WIRELESS</text>
      <text class="svc-label" x="982" y="383">NETWORKS</text>
      <text class="svc-label" x="127" y="486">DESKTOP</text>
      <text class="svc-label" x="127" y="503">SUPPORT</text>
      <text class="svc-label" x="1016" y="478">ANTIVIRUS</text>
      <text class="svc-label" x="1016" y="495">SOLUTIONS</text>
    </g>
  </svg>
  <h2 class="section-title">OUR <span>SERVICES</span></h2>
</section>

<section class="panel panel-support">
  <h3 style="left:85px"><i></i>IT SUPPORT SOLUTIONS</h3>
  <div class="divider" style="left:85px;width:488px"></div>
  <div class="photo" role="img" aria-label="Two technicians working beside server racks in a data centre" style="left:85px;background:linear-gradient(135deg,#2b4a7a,#7fa6c9)"></div>
  <p style="left:310px">Lorem ipsum dolor sit amet, consecretk etuer adipiscing elit, sed diam nonumre my nibh euismod tinciduntol ut laoret et re olore magna aliquam erat volutpt. Ut wisi minim consequat.</p>
  <div class="btn" style="left:310px;background:linear-gradient(#a5a5a5,#777)">Read More <span>&#8594;</span></div>
</section>
<section class="panel panel-outsource">
  <h3 style="left:31px"><i></i>WHY OUTSOURCE TECHNOLOGIES</h3>
  <div class="divider" style="left:31px;width:488px"></div>
  <div class="photo" role="img" aria-label="Hand holding a glowing globe surrounded by floating screens" style="left:31px;background:radial-gradient(circle at 50% 40%,#7fc4ee,#163a5e 75%)"></div>
  <p style="left:252px">Lorem ipsum dolor sit amet, consecretk etuer adipiscing elit, sed diam nonumre my nibh euismod tinciduntol ut laoret et re olore magna aliquam erat volutpt. Ut wisi minim consequat.</p>
  <div class="btn" style="left:252px;background:linear-gradient(#2aa0e4,#1480c8)">Read More <span>&#8594;</span></div>
</section>
<div class="notch"></div>

<section class="cta">
  <h2>IT Solutions That Works For Your Business</h2>
  <h3>A Full Service Technology Company</h3>
  <div class="call-btn">
    <svg width="30" height="30" viewBox="0 0 24 24"><path d="M6.6 10.8a15 15 0 0 0 6.6 6.6l2.2-2.2a1 1 0 0 1 1-.25 11.4 11.4 0 0 0 3.6.57 1 1 0 0 1 1 1V20a1 1 0 0 1-1 1A17 17 0 0 1 3 4a1 1 0 0 1 1-1h3.5a1 1 0 0 1 1 1c0 1.25.2 2.45.57 3.57a1 1 0 0 1-.25 1z" fill="#fff"/></svg>
    <div>Call Us Today<br>(555) 240-7318</div>
    <span class="sq"></span>
  </div>
</section>

<footer class="site-footer">
  <div class="abs" role="img" aria-label="Faint night city skyline behind the footer" style="inset:0;background:linear-gradient(180deg,rgba(60,70,85,.25),rgba(0,0,0,0))"></div>
  <div class="fcol quick" style="left:85px">
    <h4>Quick <span>Links</span></h4>
    <ul><li>Home</li><li>About Us</li><li>Services</li><li>Support</li><li>Clients</li><li>Careers</li><li>Contact Us</li></ul>
  </div>
  <div class="fcol contact-col" style="left:319px">
    <h4>Contact <span>Details</span></h4>
    <div class="line">Kelvanbrook Technology Group, Inc.</div>
    <div class="line" style="margin-top:8px">418 Marlow Ave.</div>
    <div class="line">Brenton, Texas 77000</div>
    <div class="row"><svg width="14" height="14" viewBox="0 0 24 24"><path d="M6.6 10.8a15 15 0 0 0 6.6 6.6l2.2-2.2a1 1 0 0 1 1-.25 11.4 11.4 0 0 0 3.6.57 1 1 0 0 1 1 1V20a1 1 0 0 1-1 1A17 17 0 0 1 3 4a1 1 0 0 1 1-1h3.5a1 1 0 0 1 1 1c0 1.25.2 2.45.57 3.57a1 1 0 0 1-.25 1z" fill="#3cb0f0"/></svg>(555) 240-7318</div>
    <div class="row"><svg width="14" height="14" viewBox="0 0 24 24"><rect x="3" y="8" width="18" height="10" fill="#3cb0f0"/><rect x="6" y="3" width="12" height="5" fill="#3cb0f0"/></svg>(555) 240-7318</div>
    <div class="row"><svg width="14" height="14" viewBox="0 0 24 24"><rect x="2" y="5" width="20" height="14" fill="#3cb0f0"/><path d="M2 5l10 8 10-8" stroke="#1f2226" stroke-width="2" fill="none"/></svg>info@kelvanbrook.com</div>
  </div>
  <div class="fcol social" style="left:655px">
    <h4>Get <span>Social</span></h4>
    <ul><li><span class="sq"></span>Friendwall</li><li><span class="sq"></span>Chirper</li><li><span class="sq"></span>Circleplus</li><li><span class="sq"></span>Linkup</li></ul>
  </div>
  <div class="footer-mark"><div class="sq"></div><span>KELVANBROOK</span></div>
</footer>
<div class="copyright">Copyright &copy; 2017 Kelvanbrook Technology Group, Inc. All Rights Reserved.</div>

</body>
</html>
```